Beekeeper needs a label for honey jars

Ciao! I'm from Como Italy
I'm a hobbyist beekeeper and I produce honey for myself and my friends.
I've named my apiary "Dado sereno," a play on words between my nickname (Dado, from Edoardo) and the Italian expression "Dado sereno," which translates to "a drizzle of honey" in English.
I need to create a label for my honey glass jars (250 gr and 500 gr).
I don't need a label for commercial purposes. I would like to include at least the name “Apicoltura Dado sereno", the type of honey (e.g., wildflower, acacia...) and a space for the production year, to be handwritten each year.
In the design some references to the world of bees.
For reference, attached a label with a style I like
Attached are the images of the selected jars and their measurements
Thanks and good job!

Target Market(s)

beekeeping, honey

Requirements
Nice to have
• I would like an elegant style with clean graphics.
Should not have
• Predominance of black color.

```html
<!DOCTYPE html>
<html lang="it">
<head>
<meta charset="utf-8">
<title>Apicoltura Dado sereno – Etichetta Millefiori</title>
<link rel="stylesheet" href="https://fonts.googleapis.com/css2?family=Oswald:wght@400;500;600&display=swap">
<style>
  :root {
    --canvas: #f3efe6;
    --label: #ffffff;
    --honey: #e8a23a;
    --honey-soft: #f6dcae;
    --comb-tint: #f4f4f2;
    --ink: #4a4a4a;
    --frame: #7a7a7a;
  }
  html, body {
    margin: 0;
    padding: 0;
    width: 1200px;
    height: 803px;
    overflow: hidden;
    background: var(--canvas);
  }
  .stage {
    position: relative;
    width: 1200px;
    height: 803px;
  }
  .label {
    position: absolute;
    left: 310px;
    top: 111px;
    width: 580px;
    height: 580px;
    box-sizing: border-box;
    background: var(--label);
    border: 7px dashed var(--frame);
    font-family: "Oswald", sans-serif;
    text-align: center;
    box-shadow: 0 0 0 10px var(--label), 0 6px 24px rgba(0,0,0,0.08);
  }
  .label__comb {
    position: absolute;
    inset: 0;
    background: radial-gradient(ellipse at 50% 55%, var(--comb-tint) 0%, var(--comb-tint) 45%, var(--label) 80%);
  }
  .label__line {
    position: absolute;
    left: 0;
    right: 0;
    margin: 0;
  }
  .label__kicker {
    top: 52px;
    font-size: 40px;
    line-height: 1;
    font-weight: 500;
    color: var(--honey);
    transform: scaleX(0.88);
  }
  .label__title {
    top: 100px;
    font-size: 76px;
    line-height: 1;
    font-weight: 600;
    color: var(--honey);
    transform: scaleX(0.9);
  }
  .label__emblem {
    position: absolute;
    left: 190px;
    top: 205px;
    width: 184px;
    height: 160px;
  }
  .label__town {
    top: 382px;
    font-size: 24px;
    line-height: 1;
    font-weight: 400;
    color: var(--ink);
    letter-spacing: 28px;
    padding-left: 28px;
  }
  .label__band {
    position: absolute;
    left: 210px;
    top: 416px;
    width: 146px;
    height: 12px;
  }
  .label__variety {
    top: 458px;
    font-size: 36px;
    line-height: 1;
    font-weight: 500;
    color: var(--ink);
    transform: scaleX(0.85);
  }
  .label__fill {
    top: 522px;
    font-size: 14px;
    line-height: 1;
    color: var(--ink);
    letter-spacing: 3px;
  }
</style>
</head>
<body>
<main class="stage">
  <section class="label">
    <div class="label__comb" role="img" aria-label="Motivo tenue a nido d'ape sullo sfondo dell'etichetta"></div>

    <p class="label__line label__kicker">APICOLTURA</p>
    <h1 class="label__line label__title">DADO SERENO</h1>

    <svg class="label__emblem" viewBox="0 0 184 160" role="img" aria-label="Illustrazione lineare di un'ape con una goccia di miele">
      <ellipse cx="92" cy="80" rx="88" ry="76" fill="var(--honey-soft)"/>
    </svg>

    <p class="label__line label__town">COMO</p>
    <svg class="label__band" viewBox="0 0 146 12" role="img" aria-label="Motivo ondulato decorativo che richiama il lago">
      <rect width="146" height="12" fill="var(--honey-soft)"/>
    </svg>

    <h2 class="label__line label__variety">MILLEFIORI</h2>
    <p class="label__line label__fill">.....gr &nbsp;|&nbsp; .....</p>
  </section>
</main>
</body>
</html>
```